Business Card for Professional Photographer

I'm looking for an eye catching modern clean design that compliments my logo/ website fonts & colours.
I specialise in architecture, corporate & commercial photography so I'm marketing to professional clients rather than portrait / wedding clients.

I would prefer to not have a solid black design.

My logo brand guide is as follows :

Main front font. : Reislust
Main font colour : #fff
Slogan front font : Ubuntu Bold
Monogram front font : Venti Medium
Container colour : #fff

I need print ready files in pdf .png & .eps formats.

Included in the files below are some screen grabs as reference to font & colours etc.

```html
<!DOCTYPE html>
<html lang="en">
<head>
<meta charset="utf-8">
<title>Clearline Studio – Business Card</title>
<link rel="stylesheet" href="https://fonts.googleapis.com/css2?family=Josefin+Sans:wght@300&family=Lato:wght@400;700;900&family=Ubuntu:wght@700&display=swap">
<style>
  :root {
    --page: #d9d9db;
    --gold-light: #f8eea2;
    --gold-mid: #d9b460;
    --gold-deep: #b8843f;
    --gold-text: #c89a4e;
    --ink: #111111;
    --paper: #ffffff;
    --body-text: #1c1c1c;
  }
  * { margin: 0; padding: 0; box-sizing: border-box; }
  html, body { width: 1200px; height: 900px; overflow: hidden; }
  body {
    background: var(--page);
    font-family: "Lato", sans-serif;
    position: relative;
  }
  .card {
    position: absolute;
    width: 520px;
    height: 300px;
    border-radius: 26px;
    box-shadow: 0 6px 18px rgba(0,0,0,0.18);
    overflow: hidden;
  }
  .card--front {
    left: 80px; top: 140px;
    background: linear-gradient(180deg, var(--gold-light) 0%, var(--gold-mid) 55%, var(--gold-deep) 100%);
  }
  .card--back {
    left: 600px; top: 460px;
    background: var(--paper);
  }
  .brand {
    position: absolute;
    display: flex;
    align-items: center;
    gap: 14px;
  }
  .brand__dot {
    width: 34px; height: 34px;
    border-radius: 50%;
    border: 3px solid currentColor;
    flex: none;
  }
  .brand__name {
    font-family: "Josefin Sans", sans-serif;
    font-weight: 300;
    letter-spacing: 0.16em;
    line-height: 1;
  }
  .brand__tagline {
    font-family: "Ubuntu", sans-serif;
    font-weight: 700;
    letter-spacing: 0.12em;
    margin-top: 4px;
  }
  .card--front .brand { left: 120px; top: 120px; color: var(--ink); }
  .card--front .brand__name { font-size: 27px; }
  .card--front .brand__tagline { font-size: 8.5px; }

  .card--back .brand { left: 40px; top: 54px; color: var(--gold-text); }
  .card--back .brand__name { font-size: 24px; }
  .card--back .brand__tagline { font-size: 8px; }

  .address {
    position: absolute;
    right: 34px; top: 64px;
    text-align: right;
    font-size: 14px;
    line-height: 1.3;
    color: var(--body-text);
  }
  .person {
    position: absolute;
    left: 40px; top: 150px;
  }
  .person__name {
    font-weight: 900;
    font-size: 19px;
    color: var(--gold-text);
    letter-spacing: 0.02em;
  }
  .person__role {
    font-size: 15px;
    color: var(--body-text);
    margin-bottom: 12px;
  }
  .contact-list { list-style: none; }
  .contact-list li {
    display: flex;
    align-items: center;
    gap: 9px;
    font-size: 15px;
    color: var(--body-text);
    line-height: 1.45;
  }
  .contact-list svg { width: 12px; height: 12px; fill: var(--gold-text); flex: none; }
</style>
</head>
<body>

  <section class="card card--front" aria-label="Card front">
    <div class="brand">
      <span class="brand__dot"></span>
      <div>
        <div class="brand__name">CLEARLINE STUDIO</div>
        <div class="brand__tagline">Architecture corporate commercial</div>
      </div>
    </div>
  </section>

  <section class="card card--back" aria-label="Card back">
    <div class="brand">
      <span class="brand__dot"></span>
      <div>
        <div class="brand__name">CLEARLINE STUDIO</div>
        <div class="brand__tagline">Architecture corporate commercial</div>
      </div>
    </div>

    <address class="address" style="font-style:normal">
      17 Harbour Row<br>Eastmere, 40218
    </address>

    <div class="person">
      <div class="person__name">DANIEL REEVES</div>
      <div class="person__role">Managing Director</div>
      <ul class="contact-list">
        <li>
          <svg viewBox="0 0 24 24" aria-hidden="true"><path d="M6.6 10.8a15 15 0 0 0 6.6 6.6l2.2-2.2a1 1 0 0 1 1-.25 11.4 11.4 0 0 0 3.6.57 1 1 0 0 1 1 1V20a1 1 0 0 1-1 1A17 17 0 0 1 3 4a1 1 0 0 1 1-1h3.5a1 1 0 0 1 1 1c0 1.25.2 2.45.57 3.57a1 1 0 0 1-.25 1z"/></svg>
          044-555 010 220
        </li>
        <li>
          <svg viewBox="0 0 24 24" aria-hidden="true"><path d="M2 5h20v14H2z M3.5 6.5 12 13l8.5-6.5" /><path d="M2 5h20v2l-10 7L2 7z" fill="#fff" opacity=".55"/></svg>
          info@clearlinestudio.com
        </li>
        <li>
          <svg viewBox="0 0 24 24" aria-hidden="true"><circle cx="12" cy="12" r="10"/></svg>
          www.clearlinestudio.com
        </li>
      </ul>
    </div>
  </section>

</body>
</html>
```